Landing Page & Email Signature

I am looking for a new landing page as well as an email signature to align with the change in business. I have included the new logo/emblem which I'd like incorporated into the design and the current landing page is www.delmorquivex.com.au should you wish to see the old version.

```html
<!DOCTYPE html>
<html lang="en">
<head>
<meta charset="utf-8">
<title>Delmor Transport – Landing Page Concepts</title>
<link href="https://fonts.googleapis.com/css2?family=Orbitron:wght@700;900&family=Roboto:wght@400;500;700&family=Roboto+Condensed:wght@700&display=swap" rel="stylesheet">
<style>
:root{
  --board:#2a2d2f;
  --red:#ae1229;
  --red-deep:#8f0d20;
  --ink:#1c1c1c;
  --footer:#161617;
  --field:#ebecee;
  --muted:#8a8a8a;
  --white:#ffffff;
  --fb:#3b5998;
  --tw:#1da1f2;
  --gp:#db4437;
}
*{box-sizing:border-box;margin:0;padding:0}
html,body{width:788px;height:1200px;overflow:hidden;background:var(--board)}
body{position:relative;font-family:"Roboto",Arial,sans-serif;color:var(--ink)}
.board-shapes{position:absolute;inset:0}
.page{position:absolute;width:307px;background:var(--white);overflow:hidden;box-shadow:0 4px 14px rgba(0,0,0,.35)}
.page--home{left:57px;top:68px;height:560px}
.page--booking{left:417px;top:68px;height:792px}
.page--contact{left:57px;top:684px;height:451px}
.abs{position:absolute}

/* header */
.site-header{position:absolute;left:0;top:0;width:307px;height:34px;background:var(--white)}
.brand{position:absolute;left:30px;top:9px}
.brand-name{font-family:"Roboto",sans-serif;font-weight:700;font-size:8.5px;color:var(--red);letter-spacing:.2px;text-transform:uppercase;white-space:nowrap}
.brand-url{font-size:2.6px;color:var(--red);margin-top:1px;letter-spacing:.1px}
.social{position:absolute;top:9px;width:7px;height:7px;border-radius:50%}
.social--a{left:179px;background:var(--fb)}
.social--b{left:187px;background:var(--tw)}
.social--c{left:196px;background:var(--gp)}
.lang{position:absolute;left:210px;top:10px;font-size:3.2px;color:#333}
.lang-dot{position:absolute;left:221px;top:9px;width:7px;height:7px;border-radius:50%;background:linear-gradient(#c8102e 50%,#f0f0f0 50%);border:.5px solid #ccc}
.nav{position:absolute;top:23px;font-size:3.4px;font-weight:700;color:#222;letter-spacing:.1px;white-space:nowrap}
.nav--home{left:151px;color:var(--red)}
.nav--services{left:170px}
.nav--quote{left:195px}
.call-panel{position:absolute;right:0;top:0;width:72px;height:34px;background:var(--red);clip-path:polygon(11% 0,100% 0,100% 100%,0 100%)}
.call-icon{position:absolute;left:12px;top:13px;width:8px;height:8px;border:.7px solid var(--white);border-radius:50%}
.call-label{position:absolute;left:24px;top:12px;font-size:3.4px;color:var(--white);font-weight:500}
.call-number{position:absolute;left:24px;top:17px;font-size:5.2px;color:var(--white);font-weight:700;white-space:nowrap}

/* hero */
.hero{position:absolute;left:0;top:34px;width:307px}
.hero-photo{position:absolute;inset:0}
.hero-caption{position:absolute;left:133px;width:145px;bottom:0;background:rgba(18,18,20,.78)}
.hero-title{font-family:"Orbitron",sans-serif;font-weight:900;color:var(--white);text-transform:uppercase;letter-spacing:.3px;line-height:1.25}
.btn-outline{position:absolute;border-radius:8px;font-size:3.2px;font-weight:700;text-transform:uppercase;display:flex;align-items:center;justify-content:center;letter-spacing:.2px}
.btn-outline--red{border:.8px solid var(--red);color:var(--red)}
.btn-outline--white{border:.8px solid var(--white);color:var(--white)}
.slider-arrow{position:absolute;width:10px;height:10px;border-radius:50%;color:var(--white);font-size:5px;display:flex;align-items:center;justify-content:center}
.slider-arrow--prev{background:#3a3a3c}
.slider-arrow--next{background:var(--red)}

/* process */
.section-title{position:absolute;left:0;width:307px;text-align:center;font-family:"Orbitron",sans-serif;font-weight:900;text-transform:uppercase;letter-spacing:.4px}
.intro{position:absolute;left:60px;width:187px;text-align:center;font-size:3.2px;line-height:1.5;color:#555}
.step{position:absolute;width:60px;text-align:center}
.step-ring{width:36px;height:36px;margin:0 auto;position:relative}
.step-label{font-size:4px;font-weight:500;color:#222;margin-top:2px}

/* contact band */
.contact-band{position:absolute;left:0;top:332px;width:307px;height:132px}
.field-white{position:absolute;background:var(--white);font-size:3.2px;color:#777;padding:3px 4px;display:flex;align-items:center}
.field-white--top{align-items:flex-start;padding-top:6px}

/* footer */
.site-footer{position:absolute;left:0;width:307px;background:var(--footer)}
.info{position:absolute;width:84px;text-align:center}
.info-ring{width:21px;height:21px;margin:0 auto;border-radius:50%;border:1.6px solid var(--red);background:var(--white);display:flex;align-items:center;justify-content:center}
.info-label{font-size:4.2px;color:var(--red);font-weight:500;margin-top:3px}
.info-text{font-size:3.3px;color:#ddd;line-height:1.6;margin-top:1px}
.footer-divider{position:absolute;width:.5px;background:#333}
.footer-rule{position:absolute;left:29px;width:249px;height:.5px;background:#333}
.copyright{position:absolute;left:0;width:307px;text-align:center;font-size:3.4px;color:#ddd}

/* booking form */
.form-heading{position:absolute;left:0;top:186px;width:307px;text-align:center;font-family:"Roboto Condensed",sans-serif;font-weight:700;font-size:8.5px;line-height:1.3;color:#1c1c1c;text-transform:uppercase}
.form-heading em{font-style:normal;color:var(--red)}
.group-title{position:absolute;left:29px;font-family:"Roboto Condensed",sans-serif;font-weight:700;font-size:6.2px;color:#1c1c1c;text-transform:uppercase}
.field{position:absolute;width:80px;height:17.6px;background:var(--field);font-size:3.2px;color:#666;display:flex;align-items:center;padding-left:8.5px}
.field--active{background:var(--white);border:.7px solid #333}
.field--white{background:var(--white)}
.field .req{color:var(--red)}
.field .chev{position:absolute;right:7px;font-size:3.5px;color:#555}
.other-band{position:absolute;left:0;top:583px;width:307px;height:112px;background:var(--red)}
.other-title{position:absolute;left:0;top:18px;width:307px;text-align:center;font-family:"Roboto Condensed",sans-serif;font-weight:700;font-size:8.5px;color:var(--white)}
.other-note{position:absolute;left:0;width:307px;text-align:center;font-size:3.3px;color:var(--white)}

/* contact page */
.how-title{font-size:8.5px;color:#1c1c1c}
.how-text{position:absolute;left:0;width:307px;text-align:center;font-size:4.2px;color:#222}
.how-link{color:var(--red);text-decoration:underline}
.contact-card{position:absolute;left:29px;top:223px;width:249px;height:107px;background:#050505}
.contact-card-side{position:absolute;left:0;top:0;width:123px;height:107px;background:var(--red)}
.card-copy{position:absolute;left:12px;top:15px;width:106px;font-size:3.2px;line-height:1.6;color:var(--white)}
.card-item{position:absolute;left:12px;font-size:3.2px;color:var(--white);display:flex;align-items:center;gap:5px}
.card-dot{width:8px;height:8px;border-radius:50%;background:var(--white);display:flex;align-items:center;justify-content:center}
.card-dot::after{content:"";width:3px;height:3px;border-radius:50%;background:var(--red)}
.enquiry-title{position:absolute;left:132px;top:13px;font-size:7px;font-weight:500;color:var(--white)}
.enquiry-field{position:absolute;background:var(--white);font-size:3.2px;color:#666;padding:0 4px;display:flex;align-items:center}
.enquiry-submit{position:absolute;left:132px;top:84px;width:23px;height:10px;background:var(--red);color:var(--white);font-size:3.2px;font-weight:700;display:flex;align-items:center;justify-content:center}
</style>
</head>
<body>

<svg class="board-shapes" width="788" height="1200" viewBox="0 0 788 1200" aria-hidden="true">
  <polygon points="606,0 676,0 363,312" fill="#ae1229"/>
  <polygon points="676,0 788,0 788,905 363,312" fill="#ae1229"/>
</svg>

<!-- ============ HOME PAGE ============ -->
<section class="page page--home">
  <header class="site-header">
    <div class="brand"><div class="brand-name">Delmor Transport</div><div class="brand-url">www.delmorquivex.com.au</div></div>
    <span class="social social--a"></span><span class="social social--b"></span><span class="social social--c"></span>
    <span class="lang">Eng ˅</span><span class="lang-dot"></span>
    <span class="nav nav--home">HOME</span><span class="nav nav--services">SERVICES</span><span class="nav nav--quote">QUOTE TEMPLATE</span>
    <div class="call-panel"><span class="call-icon"></span><span class="call-label">Call us Today :</span><span class="call-number">+1 555 010 2030</span></div>
  </header>

  <div class="hero" style="height:164px">
    <div class="hero-photo" role="img" aria-label="Cargo plane taking off over a highway bridge and port cranes at dusk" style="background:linear-gradient(180deg,#7c6a78 0%,#b07a6e 35%,#4a3a40 65%,#2a2226 100%)"></div>
    <div class="hero-caption" style="top:55px">
      <div class="hero-title" style="position:absolute;left:13px;top:13px;font-size:8.4px">We look forward<br>to satisfy your<br>current and<br>future needs!</div>
      <div class="btn-outline btn-outline--red" style="left:13px;top:61px;width:38px;height:11px">Get Started</div>
      <div class="slider-arrow slider-arrow--prev" style="left:14px;top:82px">‹</div>
      <div class="slider-arrow slider-arrow--next" style="left:30px;top:82px">›</div>
    </div>
  </div>

  <h2 class="section-title" style="top:216px;font-size:9px;color:var(--red)">Our Process</h2>
  <p class="intro" style="top:232px">Lorem ipsum dolor sit amet, consectetur adipiscing elit, sed do eiusmod tempor incididunt ut labore tempor incididunt ut labore et dolore magna aliqua.et dolore magna aliqua.</p>

  <svg class="abs" style="left:0;top:248px" width="307" height="70" viewBox="0 0 307 70" aria-hidden="true">
    <path d="M76 18 C95 12,100 25,106 35" fill="none" stroke="#555" stroke-width=".5" stroke-dasharray="1.2 1"/>
    <path d="M138 38 C150 30,155 25,168 18" fill="none" stroke="#555" stroke-width=".5" stroke-dasharray="1.2 1"/>
    <path d="M200 18 C215 14,222 25,231 35" fill="none" stroke="#555" stroke-width=".5" stroke-dasharray="1.2 1"/>
  </svg>

  <div class="step" style="left:30px;top:249px">
    <svg class="step-ring" viewBox="0 0 36 36" aria-hidden="true"><path d="M18 1 A17 17 0 0 0 18 35" fill="none" stroke="#ae1229" stroke-width="2"/><rect x="11" y="12" width="15" height="10" rx="1" fill="none" stroke="#333" stroke-width=".7" transform="rotate(-25 18 17)"/><circle cx="18" cy="17" r="2.5" fill="none" stroke="#333" stroke-width=".7"/></svg>
    <div class="step-label">Taking Order</div>
  </div>
  <div class="step" style="left:92px;top:264px">
    <svg class="step-ring" viewBox="0 0 36 36" aria-hidden="true"><path d="M18 1 A17 17 0 0 0 18 35" fill="none" stroke="#ae1229" stroke-width="2"/><circle cx="12" cy="24" r="3" fill="none" stroke="#333" stroke-width=".7"/><circle cx="25" cy="24" r="3" fill="none" stroke="#333" stroke-width=".7"/><path d="M12 24 L18 18 L25 24 M20 13 h6 v6 h-6 z" fill="none" stroke="#333" stroke-width=".7"/></svg>
    <div class="step-label">Sent Shipment</div>
  </div>
  <div class="step" style="left:154px;top:249px">
    <svg class="step-ring" viewBox="0 0 36 36" aria-hidden="true"><path d="M18 1 A17 17 0 0 0 18 35" fill="none" stroke="#ae1229" stroke-width="2"/><rect x="11" y="15" width="15" height="11" fill="none" stroke="#333" stroke-width=".7"/><rect x="10" y="12" width="17" height="3" fill="none" stroke="#333" stroke-width=".7"/><path d="M18.5 12 v14" stroke="#333" stroke-width=".7"/></svg>
    <div class="step-label">Get the Cargo</div>
  </div>
  <div class="step" style="left:217px;top:264px">
    <svg class="step-ring" viewBox="0 0 36 36" aria-hidden="true"><path d="M18 1 A17 17 0 0 0 18 35" fill="none" stroke="#ae1229" stroke-width="2"/><path d="M10 18 L18.5 10 L27 18 M12 17 v10 h13 v-10 M16 20 h5 v5 h-5 z" fill="none" stroke="#333" stroke-width=".7"/></svg>
    <div class="step-label">Delivered to door</div>
  </div>

  <div class="contact-band">
    <div class="abs" role="img" aria-label="Motorcycle detail photo tinted red" style="inset:0;background:linear-gradient(135deg,#b3172f 0%,#c4243b 45%,#a3122a 100%);clip-path:polygon(7% 0,93% 0,100% 16%,100% 100%,0 100%,0 16%)"></div>
    <h2 class="section-title" style="top:22px;left:3px;font-size:8.5px;color:var(--white)">Contact Us</h2>
    <div class="field-white" style="left:60px;top:38px;width:60px;height:14px">Name</div>
    <div class="field-white" style="left:124px;top:38px;width:60px;height:14px">Email address</div>
    <div class="field-white" style="left:187px;top:38px;width:60px;height:14px">Phone</div>
    <div class="field-white field-white--top" style="left:60px;top:55px;width:187px;height:37px">Message</div>
    <div class="btn-outline btn-outline--white" style="left:134px;top:98px;width:39px;height:12px">Submit</div>
  </div>

  <footer class="site-footer" style="top:464px;height:96px">
    <div class="footer-divider" style="left:115px;top:20px;height:53px"></div>
    <div class="footer-divider" style="left:192px;top:20px;height:53px"></div>
    <div class="info" style="left:28px;top:22px"><div class="info-ring"><svg width="7" height="9" viewBox="0 0 7 9"><path d="M3.5 0 A3.2 3.2 0 0 1 6.7 3.2 C6.7 5.5 3.5 9 3.5 9 C3.5 9 .3 5.5 .3 3.2 A3.2 3.2 0 0 1 3.5 0Z" fill="#222"/><circle cx="3.5" cy="3.2" r="1.1" fill="#fff"/></svg></div><div class="info-label">Address :</div><div class="info-text">123,Lorem ipsum dolor sit amet,<br>consectetur adipiscing</div></div>
    <div class="info" style="left:112px;top:22px"><div class="info-ring"><svg width="8" height="8" viewBox="0 0 8 8"><path d="M1.5 .5 L3 .5 L3.6 2.4 L2.6 3.2 C3.1 4.4 3.8 5.1 4.9 5.5 L5.7 4.5 L7.5 5.1 L7.5 6.6 C7.5 7.2 7 7.6 6.4 7.5 C3.5 7.1 .9 4.6 .5 1.6 C.4 1 .9 .5 1.5 .5Z" fill="#222"/></svg></div><div class="info-label">Phone :</div><div class="info-text">+61400111222</div></div>
    <div class="info" style="left:196px;top:22px"><div class="info-ring"><svg width="8" height="6" viewBox="0 0 8 6"><rect width="8" height="6" rx=".6" fill="#222"/><path d="M.5 .8 L4 3.4 L7.5 .8" fill="none" stroke="#fff" stroke-width=".6"/></svg></div><div class="info-label">Email :</div><div class="info-text">hello@delmorquivex.com.au</div></div>
    <div class="footer-rule" style="top:75px"></div>
    <div class="copyright" style="top:83px">© 2022 Company name &nbsp;| All Rights Reserved | Terms and Conditions</div>
  </footer>
</section>

<!-- ============ BOOKING PAGE ============ -->
<section class="page page--booking">
  <header class="site-header">
    <div class="brand"><div class="brand-name">Delmor Transport</div><div class="brand-url">www.delmorquivex.com.au</div></div>
    <span class="social social--a"></span><span class="social social--b"></span><span class="social social--c"></span>
    <span class="lang">Eng ˅</span><span class="lang-dot"></span>
    <span class="nav nav--home">HOME</span><span class="nav nav--services">SERVICES</span><span class="nav nav--quote">QUOTE TEMPLATE</span>
    <div class="call-panel"><span class="call-icon"></span><span class="call-label">Call us Today :</span><span class="call-number">+1 555 010 2030</span></div>
  </header>

  <div class="hero" style="height:131px">
    <div class="hero-photo" role="img" aria-label="Aerial view of a container ship at port with a jet airliner overhead" style="background:linear-gradient(100deg,#8a4a3e 0%,#4a6a78 30%,#143a46 60%,#0e2c36 100%)"></div>
    <div class="hero-caption" style="top:68px;background:rgba(18,28,32,.55)">
      <div class="hero-title" style="position:absolute;left:13px;top:8px;font-size:8.6px">Online Booking</div>
      <div class="btn-outline btn-outline--white" style="left:13px;top:24px;width:39px;height:12px">Book Now</div>
      <div class="slider-arrow slider-arrow--prev" style="left:14px;top:45px">‹</div>
      <div class="slider-arrow slider-arrow--next" style="left:30px;top:45px">›</div>
    </div>
  </div>

  <h2 class="form-heading">Please fill in &nbsp;the form below<br>to <em>make a booking.</em></h2>

  <h3 class="group-title" style="top:216px">Your Details</h3>
  <div class="field field--active" style="left:29px;top:235px">First Name<span class="req">*</span></div>
  <div class="field" style="left:114px;top:235px">Last Name<span class="req">*</span></div>
  <div class="field" style="left:199px;top:235px">Company</div>
  <div class="field" style="left:29px;top:257px">Email<span class="req">*</span></div>
  <div class="field" style="left:114px;top:257px">Phone</div>
  <div class="field" style="left:199px;top:257px">Mobile<span class="req">*</span></div>

  <h3 class="group-title" style="top:297px">Motorcycle Details</h3>
  <div class="field" style="left:29px;top:315px">Motorcycle Make<span class="req">*</span></div>
  <div class="field" style="left:114px;top:315px">Model<span class="req">*</span></div>
  <div class="field" style="left:199px;top:315px">Colour<span class="req">*</span></div>
  <div class="field" style="left:29px;top:337px">Rego / VIN<span class="req">*</span></div>
  <div class="field" style="left:114px;top:337px">Phone</div>
  <div class="field" style="left:199px;top:337px">Mobile<span class="req">*</span></div>

  <h3 class="group-title" style="top:378px">Pickup Details</h3>
  <div class="field" style="left:29px;top:397px">Address Type<span class="chev">˅</span></div>
  <div class="field" style="left:114px;top:397px">Pickup Name</div>
  <div class="field" style="left:199px;top:397px">Company Name</div>
  <div class="field" style="left:29px;top:419px">Phone</div>
  <div class="field" style="left:114px;top:419px">Pickup Address<span class="req">*</span></div>
  <div class="field" style="left:199px;top:419px">Pickup Suburb/Town<span class="req">*</span></div>
  <div class="field" style="left:29px;top:441px">Pickup City<span class="req">*</span></div>
  <div class="field" style="left:114px;top:441px">Pickup State<span class="req">*</span></div>
  <div class="field" style="left:199px;top:441px">Pickup Postcode<span class="req">*</span></div>

  <h3 class="group-title" style="top:481px">Delivery Details</h3>
  <div class="field" style="left:29px;top:499px">Address Type<span class="chev">˅</span></div>
  <div class="field" style="left:114px;top:499px">Delivery Name</div>
  <div class="field" style="left:199px;top:499px">Company Name</div>
  <div class="field" style="left:29px;top:521px">Phone</div>
  <div class="field" style="left:114px;top:521px">Delivery Address<span class="req">*</span></div>
  <div class="field" style="left:199px;top:521px">Delivery Suburb/Town<span class="req">*</span></div>
  <div class="field" style="left:29px;top:543px">Delivery City<span class="req">*</span></div>
  <div class="field" style="left:114px;top:543px">Delivery State<span class="req">*</span></div>
  <div class="field" style="left:199px;top:543px">Delivery Postcode<span class="req">*</span></div>

  <div class="other-band">
    <h3 class="other-title">OTHER</h3>
    <div class="field field--white" style="left:29px;top:36px">Pickup &nbsp;Date<span class="chev">▦</span></div>
    <div class="field field--white" style="left:114px;top:36px">Delivery Date<span class="chev">▦</span></div>
    <div class="field field--white" style="left:199px;top:36px">Add a Box ($60-$120)<span class="chev">˅</span></div>
    <p class="other-note" style="top:62px">Add Secure Payment Handover service. Driver to handover a cheque to the seller on pickup ($50)</p>
    <p class="other-note" style="top:69px">Any other information you think we will need?</p>
    <div class="btn-outline btn-outline--white" style="left:136px;top:79px;width:39px;height:12px">Quoted Price</div>
  </div>

  <footer class="site-footer" style="top:695px;height:97px">
    <div class="footer-divider" style="left:115px;top:19px;height:52px"></div>
    <div class="footer-divider" style="left:192px;top:19px;height:52px"></div>
    <div class="info" style="left:28px;top:21px"><div class="info-ring"><svg width="7" height="9" viewBox="0 0 7 9"><path d="M3.5 0 A3.2 3.2 0 0 1 6.7 3.2 C6.7 5.5 3.5 9 3.5 9 C3.5 9 .3 5.5 .3 3.2 A3.2 3.2 0 0 1 3.5 0Z" fill="#222"/><circle cx="3.5" cy="3.2" r="1.1" fill="#fff"/></svg></div><div class="info-label">Address :</div><div class="info-text">123,Lorem ipsum dolor sit amet,<br>consectetur adipiscing</div></div>
    <div class="info" style="left:112px;top:21px"><div class="info-ring"><svg width="8" height="8" viewBox="0 0 8 8"><path d="M1.5 .5 L3 .5 L3.6 2.4 L2.6 3.2 C3.1 4.4 3.8 5.1 4.9 5.5 L5.7 4.5 L7.5 5.1 L7.5 6.6 C7.5 7.2 7 7.6 6.4 7.5 C3.5 7.1 .9 4.6 .5 1.6 C.4 1 .9 .5 1.5 .5Z" fill="#222"/></svg></div><div class="info-label">Phone :</div><div class="info-text">+61400111222</div></div>
    <div class="info" style="left:196px;top:21px"><div class="info-ring"><svg width="8" height="6" viewBox="0 0 8 6"><rect width="8" height="6" rx=".6" fill="#222"/><path d="M.5 .8 L4 3.4 L7.5 .8" fill="none" stroke="#fff" stroke-width=".6"/></svg></div><div class="info-label">Email :</div><div class="info-text">hello@delmorquivex.com.au</div></div>
    <div class="footer-rule" style="top:74px"></div>
    <div class="copyright" style="top:82px">© 2022 Company name &nbsp;| All Rights Reserved | Terms and Conditions</div>
  </footer>
</section>

<!-- ============ CONTACT PAGE ============ -->
<section class="page page--contact">
  <header class="site-header">
    <div class="brand"><div class="brand-name">Delmor Transport</div><div class="brand-url">www.delmorquivex.com.au</div></div>
    <span class="social social--a"></span><span class="social social--b"></span><span class="social social--c"></span>
    <span class="lang">Eng ˅</span><span class="lang-dot"></span>
    <span class="nav nav--home">HOME</span><span class="nav nav--services">SERVICES</span><span class="nav nav--quote">QUOTE TEMPLATE</span>
    <div class="call-panel"><span class="call-icon"></span><span class="call-label">Call us Today :</span><span class="call-number">+1 555 010 2030</span></div>
  </header>

  <div class="hero" style="height:131px">
    <div class="hero-photo" role="img" aria-label="Businessman beside a truck on a highway with a glowing network map overlay" style="background:linear-gradient(100deg,#5a6e86 0%,#c9a27a 35%,#6a7890 60%,#243650 100%)"></div>
    <div class="hero-caption" style="top:68px">
      <div class="hero-title" style="position:absolute;left:13px;top:10px;font-size:8.6px">Delmor Transport</div>
      <div class="btn-outline btn-outline--red" style="left:13px;top:25px;width:38px;height:11px">Get in Touch</div>
      <div class="slider-arrow slider-arrow--prev" style="left:14px;top:45px">‹</div>
      <div class="slider-arrow slider-arrow--next" style="left:30px;top:45px">›</div>
    </div>
  </div>

  <h2 class="section-title how-title" style="top:185px">How to make contact?</h2>
  <p class="how-text" style="top:201px">The easiest way is to use the contact form below or email</p>
  <p class="how-text" style="top:209px"><span class="how-link">hello@delmorquivex.com.au</span></p>

  <div class="contact-card">
    <div class="contact-card-side">
      <p class="card-copy">If you need to contact us during this time, please email sales@ridewheelo.com.au. We will have very limited staff and delayed responses during this time as our staff enjoy their time off – thank you for your understanding.</p>
      <div class="card-item" style="top:47px"><span class="card-dot"></span>We are located in: Brindle Vale NSW 2999</div>
      <div class="card-item" style="top:60px"><span class="card-dot"></span>Office Hours: Monday – Friday 8.00am to 4.00pm</div>
      <div class="card-item" style="top:73px"><span class="card-dot"></span>Phone: 0400 111 222</div>
      <div class="card-item" style="top:86px"><span class="card-dot"></span>ABN: 11 222 333 444</div>
    </div>
    <h3 class="enquiry-title">Enquiry Form</h3>
    <div class="enquiry-field" style="left:132px;top:25px;width:107px;height:11px">Name:</div>
    <div class="enquiry-field" style="left:132px;top:40px;width:52px;height:11px">Email:</div>
    <div class="enquiry-field" style="left:187px;top:40px;width:52px;height:11px">Phone:</div>
    <div class="enquiry-field" style="left:132px;top:55px;width:107px;height:24px;align-items:flex-start;padding-top:4px">Your Message</div>
    <div class="enquiry-submit">SUBMIT</div>
  </div>

  <footer class="site-footer" style="top:353px;height:98px">
    <div class="footer-divider" style="left:115px;top:20px;height:53px"></div>
    <div class="footer-divider" style="left:192px;top:20px;height:53px"></div>
    <div class="info" style="left:28px;top:21px"><div class="info-ring"><svg width="7" height="9" viewBox="0 0 7 9"><path d="M3.5 0 A3.2 3.2 0 0 1 6.7 3.2 C6.7 5.5 3.5 9 3.5 9 C3.5 9 .3 5.5 .3 3.2 A3.2 3.2 0 0 1 3.5 0Z" fill="#222"/><circle cx="3.5" cy="3.2" r="1.1" fill="#fff"/></svg></div><div class="info-label">Address :</div><div class="info-text">123,Lorem ipsum dolor sit amet,<br>consectetur adipiscing</div></div>
    <div class="info" style="left:112px;top:21px"><div class="info-ring"><svg width="8" height="8" viewBox="0 0 8 8"><path d="M1.5 .5 L3 .5 L3.6 2.4 L2.6 3.2 C3.1 4.4 3.8 5.1 4.9 5.5 L5.7 4.5 L7.5 5.1 L7.5 6.6 C7.5 7.2 7 7.6 6.4 7.5 C3.5 7.1 .9 4.6 .5 1.6 C.4 1 .9 .5 1.5 .5Z" fill="#222"/></svg></div><div class="info-label">Phone :</div><div class="info-text">+61400111222</div></div>
    <div class="info" style="left:196px;top:21px"><div class="info-ring"><svg width="8" height="6" viewBox="0 0 8 6"><rect width="8" height="6" rx=".6" fill="#222"/><path d="M.5 .8 L4 3.4 L7.5 .8" fill="none" stroke="#fff" stroke-width=".6"/></svg></div><div class="info-label">Email :</div><div class="info-text">hello@delmorquivex.com.au</div></div>
    <div class="footer-rule" style="top:75px"></div>
    <div class="copyright" style="top:84px">© 2022 Company name &nbsp;| All Rights Reserved | Terms and Conditions</div>
  </footer>
</section>

</body>
</html>
```